Tour operator needs simple coded WordPress site (updated extra payment for coding and guaranteed)

[update 9/7/2015]
If you design a new logo and it gets accepted, even if we use another template with your logo you will get $50
[update 8/7/2015]
Update on questions about dual-language
For dual languages we are happy to set up a second site with the same designs in a second language.
For the design aspect just allow the user to switch between languages with an icon.
For the coding, a replica of the site on a second server will do (to save messing around with multiple language plugins) - we will populate it with Chinese text
[original post]
Simple coded WordPress site for tours
You can choose to design only or design and code ($340 design, $150 bonus for coding)
Open design brief - use your creativity
Will be in 2 languages (English and Chinese) but design needs only to be in one language
Winning design will be chosen only from home page, but the winner must make a second standard template page when chosen at no extra cost.
Must be responsive design
We only need homepage and standard template page design and coding, we will populate the pages
You can use design ideas from our pamphlet if you like - attached
Only a sample logo and colors on website and pamphlet - feel free to change as the current ones seem restrictive
Current website framework only to give an idea of the number of pages and basic menu structure (no need to use existing navigation style or any style at all for that matter, open brief)
http://brightwattlejourneys.com.au/
Target Market(s)
Chinese parents of kids 10-14 (the kids will take the tour)
Industry/Entity Type
Tour
Number of Pages Required
2 page
Look and feel
Each slider illustrates characteristics of the customer's brand and the style your logo design should communicate.

```html
<!DOCTYPE html>
<html lang="en">
<head>
<meta charset="utf-8">
<title>Bright Wattle Journeys</title>
<link href="https://fonts.googleapis.com/css2?family=Oswald:wght@400;500;600&family=Open+Sans:wght@400;600;700&display=swap" rel="stylesheet">
<style>
:root{
  --orange:#f6a623;
  --orange-dark:#e48f0c;
  --navy:#1f2d4b;
  --ink:#333;
  --muted:#777;
  --grey:#ececec;
  --footer:#222;
  --footer-bar:#161616;
  --white:#fff;
}
*{box-sizing:border-box;margin:0;padding:0}
html,body{width:758px;height:1200px;overflow:hidden}
body{font-family:"Open Sans",Arial,sans-serif;color:var(--ink);font-size:8px;background:var(--white)}
h2,h3,h4{font-family:"Oswald",Arial,sans-serif;font-weight:500;text-transform:uppercase}

/* hero */
.hero{position:relative;height:378px;background:linear-gradient(160deg,#9fb2c4 0%,#7d8f9f 35%,#5b5d62 65%,#3a3a3e 100%)}
.brand{position:absolute;left:22px;top:8px;width:104px;height:62px;background:var(--navy);display:flex;align-items:center;justify-content:center;text-align:center;
  font-family:"Oswald",Arial,sans-serif;font-size:13px;line-height:1.15;color:var(--white);text-transform:uppercase;padding:6px}
.lang{position:absolute;right:22px;top:12px;width:70px;height:18px;background:var(--white);font-size:8px;padding:3px 6px;display:flex;justify-content:space-between;align-items:center}
.social{position:absolute;right:104px;top:196px;display:flex;gap:8px}
.social span{width:22px;height:22px;border-radius:50%;border:2px solid var(--white)}
.tagline{position:absolute;right:40px;top:244px;width:330px;text-align:right;font-family:"Oswald",Arial,sans-serif;font-size:17px;line-height:1.3;color:var(--white);text-transform:uppercase;font-weight:500}
.nav{position:absolute;left:0;bottom:0;height:30px;width:380px;background:rgba(20,28,40,.75);display:flex;padding-left:60px}
.nav a{color:var(--white);text-decoration:none;font-size:8px;width:64px;display:flex;align-items:center;justify-content:center}
.nav a.active{background:var(--white);color:var(--ink);border-bottom:2px solid var(--orange)}

/* welcome */
.welcome{display:flex;padding:18px 22px 0 22px;height:222px;gap:30px}
.intro{flex:1}
.intro h2{font-size:15px;color:var(--ink);margin-bottom:10px}
.intro h2 em{font-style:normal;color:var(--orange)}
.intro p{font-size:7px;line-height:1.55;color:var(--muted);margin-bottom:6px}
.intro p.lead{font-weight:700;color:var(--ink)}
.btn{display:inline-block;background:var(--navy);color:var(--white);font-family:"Oswald",Arial,sans-serif;font-size:9px;padding:5px 12px;text-transform:uppercase}
.inquiry{width:180px}
.inquiry h3{font-size:14px;margin-bottom:8px}
.field{border:1px solid #ddd;height:17px;font-size:6.5px;color:#aaa;padding:4px 5px;margin-bottom:5px}
.field.tall{height:50px}
.inquiry .btn{float:right;padding:5px 18px}

/* features */
.features{background:var(--grey);height:238px;padding:18px 22px;display:flex;gap:16px}
.card{flex:1;background:var(--white);padding:12px;border-top:2px solid var(--orange)}
.card h4{font-size:9px;display:flex;align-items:center;gap:6px;margin-bottom:8px}
.card ul{list-style:none}
.card li{font-size:6.5px;line-height:1.4;color:var(--muted);margin-bottom:5px;padding-left:10px;position:relative}
.card li::before{content:"";position:absolute;left:0;top:2px;width:5px;height:5px;background:var(--orange)}
.card p{font-size:6.5px;line-height:1.5;color:var(--muted);margin-bottom:5px}

/* includes */
.includes{background:var(--orange);height:172px;padding:18px 22px;position:relative}
.includes h2{color:var(--white);font-size:16px;margin-bottom:12px}
.inc-cols{display:flex;gap:40px}
.inc-cols ul{list-style:none;width:210px}
.inc-cols li{color:var(--white);font-size:7.5px;margin-bottom:7px;display:flex;align-items:center;gap:6px}
.brochure{position:absolute;right:70px;top:62px;text-align:center;color:var(--white);font-size:6.5px;width:60px}
.doc{width:34px;height:42px;background:var(--white);margin:0 auto 4px;position:relative}
.doc::after{content:"";position:absolute;left:0;bottom:8px;width:100%;height:10px;background:#c0392b}

/* footer */
.footer{background:var(--footer);height:166px;padding:16px 22px;display:flex;gap:26px;color:#bbb}
.footer h4{color:var(--white);font-size:9px;margin-bottom:8px;font-family:"Open Sans",Arial,sans-serif;font-weight:700;text-transform:none}
.links{width:130px}
.links li{list-style:none;font-size:6.5px;margin-bottom:5px}
.news{width:160px;font-size:6.5px}
.news .input{background:var(--white);height:14px;margin:6px 0;color:#999;padding:3px 4px}
.news .sub{display:inline-block;background:var(--navy);color:var(--white);padding:3px 10px}
.contact{width:150px;font-size:6.5px}
.contact div{display:flex;gap:6px;align-items:center;margin-bottom:7px}
.seal{margin-left:auto;width:110px;height:110px;border-radius:50%;background:var(--navy);border:3px solid var(--orange);display:flex;align-items:center;justify-content:center;text-align:center;color:var(--white);font-family:"Oswald",Arial,sans-serif;font-size:11px;text-transform:uppercase;line-height:1.2}
.copyright{background:var(--footer-bar);height:24px;color:#999;font-size:6px;text-align:center;line-height:24px}
</style>
</head>
<body>

<header class="hero" role="img" aria-label="Group photo of smiling students by a harbour with a bridge in the background">
  <div class="brand">Bright Wattle Journeys</div>
  <div class="lang">English <span>▾</span></div>
  <div class="social"><span></span><span></span><span></span></div>
  <p class="tagline">Educational, safe, culturally<br>enlightening and fun</p>
  <nav class="nav">
    <a class="active">Home</a><a>About Us</a><a>Tours</a><a>Contact Us</a>
  </nav>
</header>

<section class="welcome">
  <div class="intro">
    <h2>Welcome to <em>Bright Wattle Journeys</em></h2>
    <p class="lead">At Bright Wattle Journeys we are passionate about educational travel and opportunities for students to gain academic and cultural understanding of Australia.</p>
    <p>Our tours blend classroom learning with city life, giving young travellers a safe, guided and memorable experience while improving their English.</p>
    <p>We partner with trusted schools, hosts and guides to deliver programs that build confidence, friendships and a lasting love of learning for every student we welcome.</p>
    <span class="btn">Read More</span>
  </div>
  <form class="inquiry">
    <h3>Quick Inquiry</h3>
    <div class="field">Name</div>
    <div class="field">Email</div>
    <div class="field tall">Message</div>
    <span class="btn">Submit</span>
  </form>
</section>

<section class="features">
  <article class="card">
    <h4><svg width="12" height="12"><circle cx="6" cy="6" r="6" fill="#f6a623"/></svg>Educational and Cultural</h4>
    <ul>
      <li>Professional lectures from Sydney universities</li>
      <li>Deluxe hostels and caring homestays</li>
      <li>Subjects from the Australian curriculum</li>
      <li>Free time to explore, stay and study</li>
      <li>Authentic meetings with native speakers</li>
      <li>Quizzes and fun activities</li>
    </ul>
  </article>
  <article class="card">
    <h4><svg width="12" height="12"><path d="M6 0L12 3V6C12 9 9 11 6 12C3 11 0 9 0 6V3Z" fill="#f6a623"/></svg>Safe and Secure</h4>
    <ul>
      <li>Staff will call the parents each night</li>
      <li>Staff with current first aid certificates</li>
      <li>Professional, accommodating providers</li>
      <li>Strict curfews and close supervision</li>
      <li>Verified bus and coach transport</li>
    </ul>
  </article>
  <article class="card">
    <h4><svg width="12" height="12"><path d="M1 11L11 1M6 1H11V6" stroke="#f6a623" stroke-width="2" fill="none"/></svg>Travel Insurance</h4>
    <p>Every student is covered by brightwattlejourneys.com.au travel insurance for the entire journey.</p>
    <p>Cover includes medical care, lost luggage and trip changes, so families can relax while students learn.</p>
    <p>Please ask our team for full details of the policy.</p>
  </article>
</section>

<section class="includes">
  <h2>Includes</h2>
  <div class="inc-cols">
    <ul>
      <li><svg width="8" height="8"><path d="M1 4L3 6L7 1" stroke="#fff" stroke-width="1.5" fill="none"/></svg>Return Airfare</li>
      <li><svg width="8" height="8"><path d="M1 4L3 6L7 1" stroke="#fff" stroke-width="1.5" fill="none"/></svg>Visa fees</li>
      <li><svg width="8" height="8"><path d="M1 4L3 6L7 1" stroke="#fff" stroke-width="1.5" fill="none"/></svg>Travel and medical insurance</li>
      <li><svg width="8" height="8"><path d="M1 4L3 6L7 1" stroke="#fff" stroke-width="1.5" fill="none"/></svg>Accommodation</li>
      <li><svg width="8" height="8"><path d="M1 4L3 6L7 1" stroke="#fff" stroke-width="1.5" fill="none"/></svg>Meals (breakfast, lunch and dinner)</li>
    </ul>
    <ul>
      <li><svg width="8" height="8"><path d="M1 4L3 6L7 1" stroke="#fff" stroke-width="1.5" fill="none"/></svg>Transportation</li>
      <li><svg width="8" height="8"><path d="M1 4L3 6L7 1" stroke="#fff" stroke-width="1.5" fill="none"/></svg>Entertainment and Lectures</li>
      <li><svg width="8" height="8"><path d="M1 4L3 6L7 1" stroke="#fff" stroke-width="1.5" fill="none"/></svg>Guides</li>
      <li><svg width="8" height="8"><path d="M1 4L3 6L7 1" stroke="#fff" stroke-width="1.5" fill="none"/></svg>Entry tickets and travel expenses</li>
    </ul>
  </div>
  <div class="brochure"><div class="doc"></div>Download the Brochure</div>
</section>

<footer class="footer">
  <div class="links">
    <h4>Quick Links</h4>
    <ul><li>› Home</li><li>› About Us</li><li>› Tours</li><li>› Contact Us</li></ul>
  </div>
  <div class="news">
    <h4>Subscribe To Newsletter</h4>
    <p>Get the latest tour updates by entering your email below.</p>
    <div class="input">Email Address</div>
    <span class="sub">Subscribe</span>
  </div>
  <div class="contact">
    <h4>Contact Detail</h4>
    <div><svg width="8" height="10"><path d="M4 0C1.8 0 0 1.8 0 4C0 7 4 10 4 10S8 7 8 4C8 1.8 6.2 0 4 0Z" fill="#f6a623"/></svg>12 Harbour Lane, Sydney NSW 2000</div>
    <div><svg width="9" height="9"><path d="M2 0L4 2L3 4C4 5.5 5 6 6 6L7 5L9 7L7.5 9C3 8.5 0.5 6 0 1.5Z" fill="#f6a623"/></svg>(02) 4000 7000</div>
    <div><svg width="10" height="8"><rect x="0.5" y="0.5" width="9" height="7" fill="none" stroke="#f6a623"/><path d="M0.5 0.5L5 4.5L9.5 0.5" fill="none" stroke="#f6a623"/></svg>hello@brightwattlejourneys.com.au</div>
  </div>
  <div class="seal">Bright Wattle<br>Journeys</div>
</footer>
<div class="copyright">© 2015 Bright Wattle Journeys. All rights reserved.</div>

</body>
</html>
```